Kelvara Pane Works Business Card

We need a business card design that is suitable for a Glazing Business. We Specialize in Repairing broken windows and doors and are a 24hr on call service. We manufacture Shower screens, Fly screens, Wardrobe doors, Security doors and grilles + mirrors. We stock a variety of mesh including Standard mesh, Pet resistant mesh, Tressmet & Clearweft. We would like to use a combination of Light Blue, Dark Blue, Black & White with perhaps a picture of glass breaking.

Industry/Entity Type

Business

Contact Information for Business Card

Brackwood Glass Service60B Glasshouse Rocks RdNarooma NSW 2546PH / FAX - 02 44765210MOB - 0419682350 Andrewemail - kelvarapane@fenmail.example

Font styles to use
Serif

Colors
34a7d8
0255a3
ffffff

Requirements
Must have
• logo with picture of broken or cracked glass

```html
<!DOCTYPE html>
<html lang="en">
<head>
<meta charset="utf-8">
<title>Kelvara Pane Works Business Card</title>
<link href="https://fonts.googleapis.com/css2?family=Open+Sans:wght@400;700;800&display=swap" rel="stylesheet">
<style>
  :root {
    --page-bg: #e9ebee;
    --card-white: #ffffff;
    --navy: #2c3452;
    --navy-mark: #5a6079;
    --brand-blue: #3553b0;
    --steel-grey: #5a5b5e;
    --ink: #2a2a2a;
    --icon-blue: #2f4aa3;
  }
  * { box-sizing: border-box; margin: 0; padding: 0; }
  html, body { width: 1200px; height: 900px; overflow: hidden; }
  body {
    background: var(--page-bg);
    font-family: "Open Sans", Arial, sans-serif;
    position: relative;
  }
  .card {
    position: absolute;
    left: 250px;
    width: 700px;
    height: 400px;
    box-shadow: 0 6px 18px rgba(0,0,0,0.18);
    overflow: hidden;
  }
  .card-back {
    top: 30px;
    background: var(--navy);
    display: flex;
    align-items: center;
    justify-content: center;
    padding: 40px 60px;
  }
  .card-back .wordmark {
    color: var(--navy-mark);
    font-weight: 800;
    font-size: 56px;
    line-height: 1.15;
    letter-spacing: 2px;
    text-transform: uppercase;
    text-align: center;
  }
  .card-front {
    top: 470px;
    background: var(--card-white);
  }
  .front-shapes { position: absolute; inset: 0; }
  .holder-name {
    position: absolute;
    left: 92px;
    top: 30px;
    color: var(--brand-blue);
    font-weight: 700;
    font-size: 24px;
  }
  .front-wordmark {
    position: absolute;
    right: 30px;
    top: 112px;
    width: 340px;
    text-align: center;
    color: var(--brand-blue);
    font-weight: 800;
    font-size: 38px;
    line-height: 1.15;
    text-transform: uppercase;
    letter-spacing: 1px;
  }
  .contact-list {
    position: absolute;
    left: 40px;
    top: 176px;
    list-style: none;
    color: var(--ink);
    font-size: 16px;
    line-height: 24px;
  }
  .contact-list li { display: flex; align-items: center; gap: 12px; }
  .contact-list svg { width: 12px; height: 12px; flex: none; fill: var(--icon-blue); }
</style>
</head>
<body>
  <section class="card card-back" aria-label="Card back">
    <span class="wordmark">Kelvara Pane Works</span>
  </section>

  <section class="card card-front" aria-label="Card front">
    <svg class="front-shapes" viewBox="0 0 700 400" preserveAspectRatio="none" aria-hidden="true">
      <polygon points="20,22 70,22 20,52" fill="var(--brand-blue)"/>
      <polygon points="70,22 76,22 62,68 34,68" fill="var(--steel-grey)"/>
      <polygon points="0,300 260,340 250,352 0,320" fill="var(--brand-blue)"/>
      <polygon points="262,340 700,340 700,400 236,400 236,372" fill="var(--steel-grey)"/>
    </svg>

    <h1 class="holder-name">Malcolm</h1>

    <ul class="contact-list">
      <li><svg viewBox="0 0 12 12"><rect x="3" y="0" width="6" height="12" rx="1"/></svg>0419682350</li>
      <li><svg viewBox="0 0 12 12"><rect x="1" y="3" width="10" height="8" rx="1"/><rect x="3" y="0" width="6" height="3"/></svg>02 48931067</li>
      <li><svg viewBox="0 0 12 12"><rect x="0" y="2" width="12" height="8" rx="1"/></svg>kelvarapane@fenmail.example</li>
      <li><svg viewBox="0 0 12 12"><path d="M6 0a4 4 0 0 1 4 4c0 3-4 8-4 8S2 7 2 4a4 4 0 0 1 4-4z"/></svg>17C Tindale Ridge Rd Brackwood NSW 2619</li>
    </ul>

    <div class="front-wordmark">Kelvara Pane Works</div>
  </section>
</body>
</html>
```